Local Roofing/Construction company business needs new biz card design

We need a new business card design, current cards are from the start of this operation and generic at best. We are a local Construction Company (General Contractor) with a majority of our work originating from insurance claims-exterior finish work is the main focus (Roofs-Siding-Gutters etc). Heavily involved with homeowners and the low ball offers they receive from insurance company's after a insurable event takes place. I have attached some of our original logo file(s) below.

```html
<!DOCTYPE html>
<html lang="en">
<head>
<meta charset="utf-8">
<title>Stonebay Builders – Business Card</title>
<link rel="stylesheet" href="https://fonts.googleapis.com/css2?family=Open+Sans:wght@400;600;700&display=swap">
<style>
  :root {
    --backdrop: #1c1d21;
    --brand-green: #55bd6f;
    --ink-dark: #061c21;
    --ink-deep: #0a2226;
    --emboss: #0f2c31;
    --text-light: #f4f6f5;
  }
  * { box-sizing: border-box; margin: 0; padding: 0; }
  html, body {
    width: 1200px; height: 780px; overflow: hidden;
    background: var(--backdrop);
    font-family: "Open Sans", Arial, sans-serif;
  }
  .canvas {
    position: relative; width: 1200px; height: 780px;
    display: flex; align-items: center; justify-content: center; gap: 40px;
  }
  .card {
    position: relative; width: 540px; height: 309px; overflow: hidden;
  }
  /* Front */
  .card-front {
    background: var(--brand-green);
    display: flex; align-items: center; justify-content: center;
  }
  .brand-lockup { display: flex; align-items: center; gap: 16px; }
  .brand-square { width: 34px; height: 34px; background: var(--ink-dark); }
  .brand-name {
    font-weight: 700; font-size: 40px; letter-spacing: 1px;
    color: var(--ink-dark); text-transform: uppercase; line-height: 1;
  }
  /* Back */
  .card-back { background: var(--ink-dark); }
  .accent-bar {
    position: absolute; top: 36px; right: 0; width: 22px; height: 44px;
    background: var(--brand-green);
  }
  .contact-block {
    position: absolute; top: 36px; right: 40px; text-align: right;
    color: var(--text-light);
  }
  .person-name { font-weight: 700; font-size: 30px; line-height: 1.1; }
  .person-name .first { color: var(--brand-green); }
  .person-role { font-size: 14px; font-weight: 600; margin-top: 2px; }
  .address { font-size: 13px; line-height: 1.35; margin-top: 14px; }
  .contact-list { list-style: none; margin-top: 22px; font-size: 13px; line-height: 1.6; }
  .contact-list li { display: flex; justify-content: flex-end; align-items: center; gap: 8px; }
  .contact-list svg { width: 13px; height: 13px; fill: var(--brand-green); flex: none; }
  .emboss-mark {
    position: absolute; left: 28px; bottom: 26px;
    display: flex; align-items: center; gap: 12px;
  }
  .emboss-mark .brand-square { width: 26px; height: 26px; background: var(--emboss); }
  .emboss-mark .brand-name { font-size: 28px; color: var(--emboss); }
</style>
</head>
<body>
<main class="canvas">
  <section class="card card-front" aria-label="Card front">
    <div class="brand-lockup">
      <span class="brand-square"></span>
      <span class="brand-name">Stonebay Builders</span>
    </div>
  </section>

  <section class="card card-back" aria-label="Card back">
    <span class="accent-bar"></span>
    <div class="contact-block">
      <h1 class="person-name"><span class="first">Marta</span> Kolarova</h1>
      <p class="person-role">Managing Director</p>
      <p class="address">42 Birch Hollow<br>Dr, Ashford, MO 63017</p>
      <ul class="contact-list">
        <li>555-201-4410
          <svg viewBox="0 0 24 24" aria-hidden="true"><path d="M6.6 10.8a15 15 0 0 0 6.6 6.6l2.2-2.2a1 1 0 0 1 1-.25 11.4 11.4 0 0 0 3.6.57 1 1 0 0 1 1 1V20a1 1 0 0 1-1 1A17 17 0 0 1 3 4a1 1 0 0 1 1-1h3.5a1 1 0 0 1 1 1c0 1.25.2 2.45.57 3.57a1 1 0 0 1-.25 1z"/></svg></li>
        <li>555-308-7720 (Emergency)
          <svg viewBox="0 0 24 24" aria-hidden="true"><path d="M6.6 10.8a15 15 0 0 0 6.6 6.6l2.2-2.2a1 1 0 0 1 1-.25 11.4 11.4 0 0 0 3.6.57 1 1 0 0 1 1 1V20a1 1 0 0 1-1 1A17 17 0 0 1 3 4a1 1 0 0 1 1-1h3.5a1 1 0 0 1 1 1c0 1.25.2 2.45.57 3.57a1 1 0 0 1-.25 1z"/></svg></li>
        <li>www.stonebaybuilders.com
          <svg viewBox="0 0 24 24" aria-hidden="true"><path d="M12 2a10 10 0 1 0 0 20 10 10 0 0 0 0-20zm0 2c1 0 2.3 2 2.8 5H9.2C9.7 6 11 4 12 4zm-7.7 7h3a17 17 0 0 0 0 2h-3a8 8 0 0 1 0-2zm.6 4h2.6c.3 1.3.7 2.5 1.3 3.4A8 8 0 0 1 4.9 15zm2.6-6H4.9a8 8 0 0 1 3.9-3.4c-.6.9-1 2.1-1.3 3.4zM12 20c-1 0-2.3-2-2.8-5h5.6c-.5 3-1.8 5-2.8 5zm3-7H9a15 15 0 0 1 0-2h6a15 15 0 0 1 0 2zm.2 5.4c.6-.9 1-2.1 1.3-3.4h2.6a8 8 0 0 1-3.9 3.4zM16.7 13a17 17 0 0 0 0-2h3a8 8 0 0 1 0 2zm-.2-4c-.3-1.3-.7-2.5-1.3-3.4A8 8 0 0 1 19.1 9z"/></svg></li>
        <li>info@stonebaybuilders.com
          <svg viewBox="0 0 24 24" aria-hidden="true"><path d="M3 5h18a1 1 0 0 1 1 1v12a1 1 0 0 1-1 1H3a1 1 0 0 1-1-1V6a1 1 0 0 1 1-1zm9 7.2L4.4 7H4v.6l8 5.6 8-5.6V7h-.4z"/></svg></li>
      </ul>
    </div>
    <div class="emboss-mark">
      <span class="brand-square"></span>
      <span class="brand-name">Stonebay Builders</span>
    </div>
  </section>
</main>
</body>
</html>
```